Redesign current business card for food company

i would like to redesign my business card. our company is food company, our product range from chips, juices, milk and etc (mostly dried food stuff).
I want o keep same logo but , the rest is open to new design.
you can check at our website about our company www.orvelpantry.com

Target Market(s)

most of food company

Industry/Entity Type

Business

Contact Information for Business Card

I want to keep more to blue color...

Colors
3176b5
abd036

Requirements
Must have
• our old logo
Nice to have
• we do not mind to have nice material on bus card in order to accomplish nice design. for example: using spot uv, embossed and etc.

```html
<!DOCTYPE html>
<html lang="en">
<head>
<meta charset="utf-8">
<title>Orvel Pantry – Business Card</title>
<link rel="stylesheet" href="https://fonts.googleapis.com/css2?family=Source+Sans+3:wght@400;600;700&display=swap">
<style>
  :root {
    --backdrop-top: #3b3b3b;
    --backdrop-bottom: #1d1d1d;
    --brand-blue: #1b63ad;
    --brand-blue-light: #2f86d0;
    --brand-blue-dark: #15559a;
    --brand-yellow: #f7b512;
    --brand-yellow-light: #fcd23a;
    --ink: #2a2a2a;
    --paper: #ffffff;
  }
  * { box-sizing: border-box; margin: 0; padding: 0; }
  html, body { width: 1200px; height: 900px; overflow: hidden; }
  body {
    position: relative;
    background: linear-gradient(to bottom, var(--backdrop-top), var(--backdrop-bottom));
    font-family: "Source Sans 3", "Myriad Pro", Arial, sans-serif;
  }
  .card {
    position: absolute;
    top: 306px;
    height: 271px;
    border-radius: 12px;
    overflow: hidden;
  }
  /* Front */
  .card-front { left: 150px; width: 438px; background: var(--paper); }
  .name-accent { position: absolute; left: 0; top: 37px; }
  .holder { position: absolute; left: 38px; top: 38px; }
  .holder-name { color: var(--brand-blue); font-size: 15px; font-weight: 600; line-height: 18px; }
  .holder-title { color: var(--ink); font-size: 12px; line-height: 15px; }
  .wordmark-front {
    position: absolute; right: 36px; top: 66px;
    color: var(--brand-blue); font-size: 58px; font-weight: 700;
    letter-spacing: -1px; line-height: 1;
  }
  .contact-list { position: absolute; left: 37px; top: 170px; list-style: none; }
  .contact-list li {
    display: flex; align-items: center; gap: 4px;
    color: var(--ink); font-size: 12.5px; line-height: 16px;
  }
  .contact-list svg { width: 9px; height: 9px; fill: var(--brand-blue); }
  .address {
    position: absolute; right: 43px; top: 201px;
    color: var(--ink); font-size: 12.5px; line-height: 16px; text-align: right;
  }
  .bottom-band { position: absolute; left: 0; bottom: 0; }
  /* Back */
  .card-back { left: 608px; width: 441px; background: var(--brand-blue); }
  .back-texture {
    position: absolute; inset: 0;
    background: linear-gradient(135deg, var(--brand-blue-light) 0%, var(--brand-blue) 45%, var(--brand-blue-dark) 100%);
    opacity: 0.55;
  }
  .wordmark-back {
    position: absolute; left: 0; right: 0; top: 70px;
    color: var(--paper); font-size: 84px; font-weight: 700;
    letter-spacing: -2px; text-align: center; line-height: 1;
  }
  .back-url {
    position: absolute; left: 0; right: 0; top: 186px;
    color: var(--paper); font-size: 12px; text-align: center;
  }
</style>
</head>
<body>
  <section class="card card-front" aria-label="Business card front">
    <svg class="name-accent" width="30" height="34" viewBox="0 0 30 34" aria-hidden="true">
      <polygon points="0,0 8,0 16,34 0,34" fill="var(--brand-yellow)"/>
      <polygon points="11,0 30,0 30,34 19,34" fill="var(--brand-blue)"/>
    </svg>
    <div class="holder">
      <p class="holder-name">Marcus Hallidan</p>
      <p class="holder-title">President</p>
    </div>
    <p class="wordmark-front">orvel</p>
    <ul class="contact-list">
      <li><svg viewBox="0 0 10 10"><path d="M1 3c0-1 1-2 4-2s4 1 4 2v1H7V3H3v1H1zM2 5h6l1 4H1z"/></svg>555 014 2231</li>
      <li><svg viewBox="0 0 10 10"><path d="M3 0h4v3H3zM1 3h8v6H1zM3 5v2h4V5z"/></svg>555 014 2237</li>
      <li><svg viewBox="0 0 10 10"><path d="M3 0h4a1 1 0 0 1 1 1v8a1 1 0 0 1-1 1H3a1 1 0 0 1-1-1V1a1 1 0 0 1 1-1zm0 1v7h4V1z"/></svg>555 017 4408</li>
      <li><svg viewBox="0 0 10 10"><path d="M0 2h10v6H0zM1 3l4 3 4-3z"/></svg>Marcus@orvelpantry.com</li>
    </ul>
    <p class="address">482 Alder Row<br>Fairbrook CA 91800</p>
    <svg class="bottom-band" width="438" height="16" viewBox="0 0 438 16" aria-hidden="true">
      <defs>
        <linearGradient id="band-yellow" x1="0" y1="0" x2="0" y2="1">
          <stop offset="0" stop-color="var(--brand-yellow-light)"/>
          <stop offset="1" stop-color="var(--brand-yellow)"/>
        </linearGradient>
        <linearGradient id="band-blue" x1="0" y1="0" x2="0" y2="1">
          <stop offset="0" stop-color="var(--brand-blue-light)"/>
          <stop offset="1" stop-color="var(--brand-blue)"/>
        </linearGradient>
      </defs>
      <polygon points="0,0 218,0 206,16 0,16" fill="url(#band-yellow)"/>
      <polygon points="222,0 438,0 438,16 210,16" fill="url(#band-blue)"/>
    </svg>
  </section>

  <section class="card card-back" aria-label="Business card back">
    <div class="back-texture" role="img" aria-label="Faint repeating leaf pattern in lighter blue"></div>
    <p class="wordmark-back">orvel</p>
    <p class="back-url">www.orvelpantry.com</p>
  </section>
</body>
</html>
```